Business Card for a mobile physiotherapy company

I need a layout for a business card for a mobile physiotherapy company.
Slogan is "Mobile Physiotherapy - Your Road To Recovery"
Phone number is 867-555-0142
Email VardenTherapy@postnest.ca (subject to change with website)
Website www.VardenTherapy.ca
My name and credentials: Luke Varden Luke Varden, BSc(kin), MPT, CAFCI, IMS
Information maybe included: Direct Billing, Services including Physiotherapy, IMS, acupuncture
Maybe include facebook and instagram logos
One side with the logo clean and sharp
Other side with details, try not to look too busy, keep everything concise

```html
<!DOCTYPE html>
<html lang="en">
<head>
<meta charset="utf-8">
<title>Varden Therapy – Business Card</title>
<link rel="stylesheet" href="https://fonts.googleapis.com/css2?family=Libre+Baskerville:wght@400;700&display=swap">
<style>
  :root {
    --green: #12574b;
    --navy: #2a4673;
    --white: #ffffff;
    --paper: #fbfbfb;
    --bg: #e6e7e9;
    --ink-soft: #2f4466;
  }
  * { box-sizing: border-box; margin: 0; padding: 0; }
  html, body { width: 1200px; height: 815px; overflow: hidden; }
  body {
    background: var(--bg);
    font-family: "Libre Baskerville", "Times New Roman", serif;
    display: flex;
    align-items: center;
    justify-content: center;
    gap: 40px;
  }
  .card {
    position: relative;
    width: 560px;
    height: 320px;
    overflow: hidden;
    box-shadow: 0 6px 18px rgba(0,0,0,.18);
  }

  /* Details side */
  .card--details { background: var(--paper); }
  .brand {
    position: absolute;
    left: 20px;
    top: 128px;
    width: 210px;
    text-align: center;
    color: var(--green);
    font-weight: 700;
    font-size: 19px;
    line-height: 1.2;
    white-space: nowrap;
  }
  .divider {
    position: absolute;
    left: 250px;
    top: 78px;
    width: 2px;
    height: 128px;
    background: var(--navy);
  }
  .person { position: absolute; left: 280px; top: 86px; }
  .person__name { font-size: 27px; font-weight: 700; letter-spacing: 1px; color: var(--navy); line-height: 1; }
  .person__name span { color: var(--green); }
  .person__creds { font-size: 10px; color: var(--ink-soft); margin-top: 6px; letter-spacing: .3px; }
  .contacts { list-style: none; margin-top: 24px; }
  .contacts li {
    display: flex;
    align-items: center;
    gap: 10px;
    font-size: 13px;
    color: var(--navy);
    letter-spacing: .6px;
    margin-bottom: 4px;
  }
  .contacts svg { width: 12px; height: 12px; fill: var(--green); flex: none; }
  .social { position: absolute; left: 113px; top: 246px; display: flex; gap: 8px; }
  .social__box { width: 24px; height: 24px; border-radius: 5px; background: var(--navy); }
  .social__box--alt { background: var(--green); }
  .band { position: absolute; left: 0; right: 0; bottom: 0; height: 14px; display: flex; }
  .band__green { width: 25%; background: var(--green); }
  .band__navy { flex: 1; background: var(--navy); }

  /* Logo side */
  .card--logo {
    background: var(--green);
    display: flex;
    align-items: center;
    justify-content: center;
    gap: 16px;
    color: var(--white);
  }
  .card--logo .brand__mark {
    width: 22px;
    height: 22px;
    background: var(--white);
  }
  .card--logo .brand__name {
    font-size: 38px;
    font-weight: 700;
    line-height: 1;
    white-space: nowrap;
  }
</style>
</head>
<body>
  <section class="card card--details">
    <div class="brand">Varden Therapy</div>
    <div class="divider"></div>
    <div class="person">
      <h1 class="person__name">LUKE <span>VARDEN</span></h1>
      <p class="person__creds">Luke Varden, BSc(kin), MPT, CAFCI, IMS</p>
      <ul class="contacts">
        <li>
          <svg viewBox="0 0 24 24" aria-hidden="true"><path d="M6.6 10.8a15.1 15.1 0 0 0 6.6 6.6l2.2-2.2a1 1 0 0 1 1-.25 11.4 11.4 0 0 0 3.6.57 1 1 0 0 1 1 1V20a1 1 0 0 1-1 1A17 17 0 0 1 3 4a1 1 0 0 1 1-1h3.5a1 1 0 0 1 1 1c0 1.25.2 2.45.57 3.57a1 1 0 0 1-.25 1z"/></svg>
          867-555-0142
        </li>
        <li>
          <svg viewBox="0 0 24 24" aria-hidden="true"><path d="M2 5h20v14H2zm2 2v.5l8 5 8-5V7l-8 5z"/></svg>
          VardenTherapy@postnest.ca
        </li>
        <li>
          <svg viewBox="0 0 24 24" aria-hidden="true"><path d="M12 2a10 10 0 1 0 0 20 10 10 0 0 0 0-20zm-1 2.1V8H7.3A8 8 0 0 1 11 4.1zm2 0A8 8 0 0 1 16.7 8H13zM4.6 10H11v4H4.6a8 8 0 0 1 0-4zm8.4 0h6.4a8 8 0 0 1 0 4H13zM7.3 16H11v3.9A8 8 0 0 1 7.3 16zm5.7 0h3.7a8 8 0 0 1-3.7 3.9z"/></svg>
          www.VardenTherapy.ca
        </li>
      </ul>
    </div>
    <div class="social" aria-label="Social media links">
      <span class="social__box"></span>
      <span class="social__box social__box--alt"></span>
    </div>
    <div class="band"><span class="band__green"></span><span class="band__navy"></span></div>
  </section>

  <section class="card card--logo">
    <span class="brand__mark"></span>
    <span class="brand__name">Varden Therapy</span>
  </section>
</body>
</html>
```